Lumavento business card

We need a modern business card - With our 4 colors - See web: www.lumavento.dk

I have attached logo and som old business Cards we have - Lets Make the new ones shine...:-) -

Industry/Entity Type

Business

Requirements
Must have
• the logo with lumavento only,

```html
<!DOCTYPE html>
<html lang="da">
<head>
<meta charset="utf-8">
<title>Lumavento business card</title>
<link rel="stylesheet" href="https://fonts.googleapis.com/css2?family=Josefin+Sans:wght@300;400&display=swap">
<style>
  :root {
    --page: #e9e6e1;
    --card: #131313;
    --green: #7fcb4f;
    --purple: #7d3690;
    --pink: #c8338c;
    --orange: #e88536;
    --text-green: #86cf55;
  }
  * { margin: 0; padding: 0; box-sizing: border-box; }
  html, body {
    width: 1200px; height: 1023px; overflow: hidden;
    background: var(--page);
    font-family: "Josefin Sans", sans-serif;
    font-weight: 300;
  }
  .sheet {
    width: 1200px; height: 1023px;
    display: flex; flex-direction: column; align-items: center; justify-content: center;
    gap: 70px;
  }
  .card {
    position: relative;
    width: 700px; height: 400px;
    background: var(--card);
    box-shadow: 0 10px 30px rgba(0,0,0,.18);
    overflow: hidden;
  }
  .tab { position: absolute; width: 72px; height: 86px; }
  .tab--pink   { right: 0; top: 30px;  background: var(--pink); }
  .tab--orange { right: 0; top: 116px; background: var(--orange); }
  .tab--green  { left: 0;  bottom: 116px; background: var(--green); }
  .tab--purple { left: 0;  bottom: 30px;  background: var(--purple); }

  .brand {
    position: absolute; left: 50%; top: 50%;
    transform: translate(-50%, -50%);
    display: flex; align-items: center; gap: 18px;
  }
  .brand__dot {
    width: 34px; height: 34px; border-radius: 50%;
    background: var(--text-green);
  }
  .brand__name {
    color: var(--text-green);
    font-size: 44px; letter-spacing: 4px;
  }

  .contact {
    position: absolute; left: 140px; top: 80px;
    color: var(--text-green);
  }
  .contact__name {
    color: var(--orange);
    font-size: 34px; letter-spacing: 2px; margin-bottom: 40px;
  }
  .contact__line { font-size: 24px; letter-spacing: 1.5px; line-height: 38px; }
</style>
</head>
<body>
<main class="sheet">
  <section class="card card--front" aria-label="Card front">
    <div class="tab tab--pink"></div>
    <div class="tab tab--orange"></div>
    <div class="tab tab--green"></div>
    <div class="tab tab--purple"></div>
    <div class="brand">
      <span class="brand__dot"></span>
      <span class="brand__name">lumavento</span>
    </div>
  </section>

  <section class="card card--back" aria-label="Card back">
    <div class="tab tab--pink"></div>
    <div class="tab tab--orange"></div>
    <div class="tab tab--green"></div>
    <div class="tab tab--purple"></div>
    <div class="contact">
      <p class="contact__name">Emma Holt</p>
      <p class="contact__line">Lindevej 14</p>
      <p class="contact__line">2500 Valby</p>
      <p class="contact__line">+45 72 48 30 67</p>
      <p class="contact__line">www.lumavento.dk</p>
    </div>
  </section>
</main>
</body>
</html>
```